National Sales - Pick Up Truck Dealer

We need a logo design for a new vehicle dealership based in Sydney, Australia. The business name is Coastal Iron Haulers Motor Co. We will be selling American 'trucks/pick up trucks' like KRV, Torvan, Blaxer, Morrow T420, Kenzo Raptors, Morrow T640 and the likes.

These vehicles are a luxury option and we would like the logo to be strong, luxurious and masculine.Colours will be black and red or black and blue with the option of grey and white.

Target Market(s)

Men

Industry/Entity Type

Car Dealer

Contact Information for Business Card

Dennis Harlowe
Managing Director
0412 639 274
den@qelvtrk.com.au

Level 8, Brindle Parkway
17 Pemberly Lane
Tarrowby Heights
KVR
Australia
Licence No: MD493152

Back of the card

qelvtrk.com.au

Font styles to use
Sans Serif

Colors

Designer to choose colors to be used in the design.

Requirements
Must have
• The company logo that is in the attachments, you can choose from the three which one you would like to work with. Must have vehicle images ....Please look at the attachments as they show examples of what we like and also provides potential images. If you choose to put an image on the front even if it is just the front of the vehicle can you please use the Black KRV Sorrento. Must have all details from the business card details section front and back
Nice to have
• N/A
Should not have
• No cars or standard trucks, please refer to the attached images to understand the product . Should not have any new logos or branding. No other colours besides what is in the logo you choose.

```html
<!DOCTYPE html>
<html lang="en">
<head>
<meta charset="utf-8">
<title>Coastal Iron Haulers Motor Co – Business Card</title>
<link rel="stylesheet" href="https://fonts.googleapis.com/css2?family=Open+Sans:wght@400;600&family=Oswald:wght@600&display=swap">
<style>
  :root {
    --backdrop: #3a3a3a;
    --card: #262626;
    --emboss: #3c3c3c;
    --white: #f2f2f2;
    --soft: #cfcfcf;
    --blue: #1a78c8;
  }
  * { margin: 0; padding: 0; box-sizing: border-box; }
  html, body { width: 1200px; height: 900px; overflow: hidden; }
  body {
    background: var(--backdrop);
    font-family: "Open Sans", Arial, sans-serif;
    position: relative;
  }
  .card {
    position: absolute;
    left: 250px;
    width: 700px;
    height: 400px;
    background: var(--card);
    box-shadow: 0 6px 18px rgba(0,0,0,0.45);
    overflow: hidden;
  }
  .card--back { top: 30px; }
  .card--front { top: 470px; }

  /* Back */
  .back-wordmark {
    position: absolute;
    top: 140px; left: 0; width: 100%;
    text-align: center;
    font-weight: 600;
    font-size: 30px;
    letter-spacing: 1px;
    color: var(--emboss);
    line-height: 1.3;
  }
  .back-web {
    position: absolute;
    bottom: 36px; left: 0; width: 100%;
    text-align: center;
    font-size: 15px;
    letter-spacing: 2px;
    color: var(--soft);
  }
  .accent { color: var(--blue); }

  /* Front */
  .front-wordmark {
    position: absolute;
    top: 48px; right: 50px;
    width: 340px;
    display: flex;
    align-items: center;
    justify-content: center;
    gap: 12px;
    font-weight: 600;
    font-size: 26px;
    line-height: 1.3;
    color: var(--white);
    text-align: center;
  }
  .mark-dot {
    width: 12px; height: 12px;
    border-radius: 50%;
    background: var(--white);
    flex: none;
  }
  .person {
    position: absolute;
    left: 50px; top: 130px;
  }
  .person__name {
    font-family: "Oswald", "Arial Narrow", sans-serif;
    font-weight: 600;
    font-size: 40px;
    line-height: 1;
    color: var(--blue);
    text-transform: uppercase;
  }
  .person__role {
    font-weight: 600;
    font-size: 18px;
    color: var(--white);
    margin-top: 2px;
  }
  .rule {
    position: absolute;
    left: 235px; right: 40px; top: 206px;
    height: 1px;
    background: var(--soft);
  }
  .licence {
    position: absolute;
    right: 40px; top: 180px;
    font-size: 16px;
    color: var(--soft);
  }
  .licence .accent { margin-right: 4px; }
  .contacts {
    position: absolute;
    left: 50px; top: 222px;
    list-style: none;
  }
  .contacts li {
    display: flex;
    align-items: center;
    font-size: 15px;
    color: var(--soft);
    height: 27px;
    letter-spacing: 0.5px;
  }
  .contacts svg { width: 16px; height: 16px; margin-right: 14px; flex: none; }
  .address {
    position: absolute;
    right: 40px; top: 222px;
    text-align: right;
    font-size: 15px;
    line-height: 1.6;
    color: var(--soft);
    font-style: normal;
  }
  .band {
    position: absolute;
    left: 0; right: 0; bottom: 0;
    height: 12px;
    background: var(--blue);
  }
</style>
</head>
<body>

<section class="card card--back" aria-label="Card back">
  <div class="back-wordmark">Coastal Iron Haulers<br>Motor Co</div>
  <div class="back-web">www.<span class="accent">qelvtrk</span>.com.au</div>
</section>

<section class="card card--front" aria-label="Card front">
  <div class="front-wordmark"><span class="mark-dot"></span><span>Coastal Iron Haulers<br>Motor Co</span></div>

  <div class="person">
    <h1 class="person__name">Dennis Harlowe</h1>
    <p class="person__role">Managing Director</p>
  </div>

  <div class="rule"></div>
  <p class="licence"><span class="accent">Licence No:</span>MD493152</p>

  <ul class="contacts">
    <li>
      <svg viewBox="0 0 16 16" aria-hidden="true"><rect x="4" y="1" width="8" height="14" rx="1.5" fill="none" stroke="#1a78c8" stroke-width="1.5"/><line x1="7" y1="12.5" x2="9" y2="12.5" stroke="#1a78c8" stroke-width="1.5"/></svg>
      0412 639 274
    </li>
    <li>
      <svg viewBox="0 0 16 16" aria-hidden="true"><rect x="1" y="3" width="14" height="10" fill="none" stroke="#1a78c8" stroke-width="1.5"/><polyline points="1,3 8,9 15,3" fill="none" stroke="#1a78c8" stroke-width="1.5"/></svg>
      den@qelvtrk.com.au
    </li>
    <li>
      <svg viewBox="0 0 16 16" aria-hidden="true"><circle cx="8" cy="8" r="6.5" fill="none" stroke="#1a78c8" stroke-width="1.5"/><ellipse cx="8" cy="8" rx="2.8" ry="6.5" fill="none" stroke="#1a78c8" stroke-width="1.2"/><line x1="1.5" y1="8" x2="14.5" y2="8" stroke="#1a78c8" stroke-width="1.2"/></svg>
      <span>www.<span class="accent">qelvtrk</span>.com.au</span>
    </li>
  </ul>

  <address class="address">
    Level 8, Brindle Parkway,<br>
    17 Pemberly Lane, Tarrowby Heights,<br>
    KVR, Australia
  </address>

  <div class="band"></div>
</section>

</body>
</html>
```